National appliance rental company needs a newspaper ad design

We need an ad template that we can use for different newspaper advertising. Ad is to be colourful - I have attached our current marketing so you have an idea of colours.
Text to be something like the below:

Want it, Rent it, Own it!

Need to update your furniture? Kids need stuff for school?

(Put in pics of phones and TV)

Zelvos starting from just $8 per week
Smart phones starting from $10 per week
Large family fridges from $30 per week

TV’s, laptops, whitegoods, furniture, beds – we will finance just about anything!

Fast approvals – call 1300 582 967 or go to www.brightwellhomeleasing.com.au/apply - NOW!
$50 credit voucher given to the first 10 successful applicants.

(Pic of logo somewhere)
Terms and conditions apply. Pricing based on 24 month term

Brightwell Home Leasing P/L ACN 061 847 293. Australian Credit Licence # 718294

Target Market(s)

Low income people and families

Industry/Entity Type

Appliance

Requirements
Must have
• I would love to have a couple of different sizes.
• Maybe 6cm x 10 cm, and also 10cms x 10cms.
Nice to have
• Please use the green from fridge magnet and colours from our logo, etc.

```html
<!DOCTYPE html>
<html lang="en">
<head>
<meta charset="utf-8">
<title>Brightwell Home Leasing – Newspaper Ad</title>
<link rel="stylesheet" href="https://fonts.googleapis.com/css2?family=Fredoka+One&family=Arimo:ital,wght@0,400;0,700;1,400&display=swap">
<style>
  :root {
    --page: #e9e4dc;
    --sky-light: #7fc3ee;
    --sky-dark: #1f6fb8;
    --cream: #fdf4c8;
    --red: #e0232b;
    --blue: #1577c1;
    --green: #72b53f;
    --yellow: #f8c51c;
    --price: #ffe21a;
    --ink: #1b1b1b;
    --white: #ffffff;
    --machine: #e4e6e8;
    --screen: #2a2d33;
    --fridge: #eef0f2;
  }
  * { margin: 0; padding: 0; box-sizing: border-box; }
  html, body { width: 1200px; height: 1000px; overflow: hidden; background: var(--page); }
  body { position: relative; font-family: "Arimo", Arial, sans-serif; }

  .ad { position: absolute; left: 115px; top: 15px; width: 967px; height: 967px; background: var(--cream); overflow: hidden; box-shadow: 0 2px 8px rgba(0,0,0,.25); }
  .ad > * { position: absolute; }

  .header { left: 0; top: 0; width: 967px; height: 282px; background: radial-gradient(ellipse at 45% 45%, var(--sky-light), var(--sky-dark) 85%); border-bottom: 8px solid var(--red); }

  .mascot { left: 62px; top: 15px; width: 165px; height: 245px; border-radius: 14px; background: linear-gradient(135deg, var(--white), var(--fridge) 60%, #c9cdd2); }
  .washer { left: 723px; top: 23px; width: 184px; height: 224px; border-radius: 8px; background: radial-gradient(circle at 50% 58%, #9aa3ab 0 28%, var(--machine) 30%, #f7f8f9 80%); }
  .tv-phones { left: 695px; top: 243px; width: 232px; height: 237px; border-radius: 6px; background: linear-gradient(160deg, #4a4f58, var(--screen) 55%, #111); }

  .brand { left: 255px; top: 80px; width: 420px; font-weight: 700; font-size: 56px; line-height: 62px; color: var(--white); }

  .headline { left: 10px; top: 310px; width: 600px; text-align: center; white-space: nowrap; font-family: "Fredoka One", "Arial Rounded MT Bold", sans-serif; font-weight: 400; font-size: 80px; line-height: 100px; color: var(--red); text-shadow: 3px 3px 0 var(--white), -3px -3px 0 var(--white), 3px -3px 0 var(--white), -3px 3px 0 var(--white), 0 5px 0 var(--white), 5px 0 0 var(--white), -5px 0 0 var(--white), 0 -5px 0 var(--white), 4px 9px 8px rgba(0,0,0,.35); }

  .subline { left: 110px; top: 523px; width: 500px; text-align: center; font-weight: 700; font-size: 20px; line-height: 25px; color: var(--ink); }

  .offer { left: 20px; width: 328px; height: 68px; border: 3px solid var(--white); border-radius: 10px; color: var(--white); font-size: 26px; line-height: 29px; text-align: center; padding-top: 4px; box-shadow: 0 1px 3px rgba(0,0,0,.25); }
  .offer b { color: var(--price); font-weight: 700; }
  .offer-zelvos { top: 582px; background: var(--red); }
  .offer-phones { top: 660px; background: var(--blue); }
  .offer-fridges { top: 738px; background: var(--green); }

  .finance { left: 362px; top: 582px; width: 300px; height: 226px; background: var(--blue); border: 3px solid var(--white); border-radius: 10px; color: var(--white); font-size: 26px; line-height: 30px; text-align: center; padding: 20px 40px 0; }

  .voucher { left: 630px; top: 505px; width: 370px; height: 370px; border-radius: 50%; background: var(--yellow); border: 5px solid var(--white); }
  .voucher-text { left: 660px; top: 576px; width: 300px; text-align: center; font-weight: 700; font-size: 37px; line-height: 42px; color: var(--red); }

  .approvals { left: 0; top: 825px; width: 967px; height: 90px; background: var(--green); text-align: center; }
  .approvals-title { display: block; margin-top: 12px; font-weight: 700; font-size: 36px; line-height: 38px; color: var(--red); text-shadow: 2px 2px 0 var(--white), -2px -2px 0 var(--white), 2px -2px 0 var(--white), -2px 2px 0 var(--white); }
  .approvals-contact { display: block; margin-top: 4px; font-size: 22px; color: var(--ink); }
  .approvals-contact b { font-size: 23px; }
  .approvals-contact .now { font-size: 26px; }

  .legal { left: 0; top: 915px; width: 967px; height: 52px; background: var(--red); border-top: 3px solid var(--white); color: var(--white); text-align: center; font-size: 14.5px; line-height: 18px; padding-top: 7px; }
</style>
</head>
<body>
  <main class="ad">
    <header class="header"></header>
    <div class="mascot" role="img" aria-label="Cartoon fridge mascot pointing upward"></div>
    <div class="brand">Brightwell<br>Home Leasing</div>
    <div class="washer" role="img" aria-label="Photo of a white front-loading washing machine"></div>
    <div class="tv-phones" role="img" aria-label="Photo of a flat-screen TV with three smartphones in front"></div>

    <h1 class="headline">Want it, Rent it,<br>Own it!</h1>
    <p class="subline">Need to update your furniture?<br>Kids need stuff for school?</p>

    <div class="offer offer-zelvos">Zelvos starting from<br>just <b>$8</b> per week</div>
    <div class="offer offer-phones">Smart phones starting<br>from <b>$10</b> per week</div>
    <div class="offer offer-fridges">Large family fridges<br>from <b>$30</b> per week</div>

    <div class="finance">TV’s, laptops,<br>whitegoods,<br>furniture, beds –<br>we will finance<br>just about<br>anything!</div>

    <div class="voucher"></div>
    <p class="voucher-text">$50 credit<br>voucher given<br>to the first<br>10 successful<br>applicants.</p>

    <section class="approvals">
      <strong class="approvals-title">FAST APPROVALS</strong>
      <span class="approvals-contact">call <b>1300 582 967</b> or go to <b>www.brightwellhomeleasing.com.au/apply</b> - <b class="now">NOW!</b></span>
    </section>

    <footer class="legal">Terms and conditions apply. Pricing based on 24 month term<br>Brightwell Home Leasing P/L ACN 061 847 293. Australian Credit Licence # 718294</footer>
  </main>
</body>
</html>
```